Help our Sugar Loom find our winning design! We're looking for a business card....

We’re a Sugar Loom in NY specializing in custom-made cakes and unique desserts.
Our cakes combine flavor and art, each designed to match customer’s special event and theme.
We’d like a unique business card with a clean design that will combine French chic and artistic look & feel.
We’d like to differentiate ourselves from standard bakeries, please don’t offer cupcake images :-)
Our logo is peach-pink and brown and we’d love to use these colors ( . Another color that can be added is gold - or feel free to suggest!

Target Market(s)

Women, ages 25-55

Industry/Entity Type

Boutique

Contact Information for Business Card

Text on card:
Logo
Sugar Loom by Dana Welch

www.sugarloomsweets.com
hello@sugarloom.com
(516) 555-0147
F – sugarloomnyc
IG - sugarloom_ny

Font styles to use
Sans Serif
Script

Requirements
Must have
• Logo
• Clean look
• French chic and artistic look & feel.
Nice to have
• Damask pattern
Should not have
• Cupcake images

```html
<!DOCTYPE html>
<html lang="en">
<head>
<meta charset="utf-8">
<title>Sugar Loom – Business Card</title>
<link href="https://fonts.googleapis.com/css2?family=Great+Vibes&family=Open+Sans:wght@400;600&display=swap" rel="stylesheet">
<style>
  :root {
    --backdrop: #e4e4e4;
    --blush: #e2a9b0;
    --magenta: #d9197f;
    --peach: #eaa08f;
    --cocoa: #3a2a26;
    --ink: #2b2b2b;
    --gold-dark: #a8822c;
    --gold-light: #e8cf7a;
    --paper: #ffffff;
    --swirl: #f6e6e8;
  }
  * { box-sizing: border-box; margin: 0; padding: 0; }
  html, body { width: 1200px; height: 852px; overflow: hidden; }
  body {
    background: var(--backdrop);
    font-family: "Open Sans", Arial, sans-serif;
    color: var(--ink);
    position: relative;
  }
  .card {
    position: absolute;
    top: 272px;
    width: 540px;
    height: 308px;
    border-radius: 20px;
    overflow: hidden;
    box-shadow: 0 6px 18px rgba(0,0,0,.18);
  }
  /* Front */
  .card--front { left: 40px; background: var(--blush); }
  .front__band {
    position: absolute; left: 0; right: 0; top: 130px; height: 48px;
    background: var(--magenta);
    border-top: 2px solid rgba(255,255,255,.7);
    border-bottom: 2px solid rgba(255,255,255,.7);
    box-shadow: inset 0 5px 0 var(--magenta), inset 0 -5px 0 var(--magenta);
  }
  .front__label {
    position: absolute; left: 110px; top: 72px; width: 320px; height: 164px;
    background: var(--paper);
    border-radius: 60px;
    border: 2px solid var(--peach);
    box-shadow: 0 0 0 6px var(--paper), 0 4px 10px rgba(0,0,0,.2);
    display: flex; align-items: center; justify-content: center;
  }
  .brand-name {
    font-family: "Great Vibes", cursive;
    font-weight: 400;
    color: var(--cocoa);
    white-space: nowrap;
  }
  .front__label .brand-name { font-size: 58px; }

  /* Back */
  .card--back { left: 620px; background: var(--paper); }
  .back__swirl {
    position: absolute; left: 20px; top: 40px; width: 190px; height: 210px;
    border-radius: 50% 40% 50% 30%;
    background: radial-gradient(ellipse at center, var(--swirl) 0%, rgba(246,230,232,0) 70%);
  }
  .back__brand {
    position: absolute; right: 44px; top: 34px; width: 230px; height: 92px;
    border: 1.5px solid var(--peach);
    border-radius: 46px;
    display: flex; align-items: center; justify-content: center;
  }
  .back__brand .brand-name { font-size: 44px; }
  .back__rule {
    position: absolute; left: 216px; right: 40px; top: 150px; height: 3px;
    background: linear-gradient(90deg, var(--gold-dark), var(--gold-light) 55%, var(--gold-dark));
  }
  .back__owner { position: absolute; left: 30px; top: 134px; }
  .owner__line { font-size: 15px; line-height: 1.1; }
  .owner__name {
    font-family: "Great Vibes", cursive;
    font-size: 32px; line-height: 1; color: var(--ink);
  }
  .contact-list {
    position: absolute; left: 30px; top: 214px; list-style: none;
    font-size: 14px; line-height: 24px;
  }
  .contact-list li, .social-list li { display: flex; align-items: center; gap: 8px; }
  .contact-list svg { width: 13px; height: 13px; fill: var(--ink); }
  .social-list {
    position: absolute; right: 40px; top: 166px; list-style: none;
    font-size: 14px; line-height: 22px;
  }
  .social-mark { width: 11px; height: 11px; background: var(--ink); border-radius: 2px; }
</style>
</head>
<body>
  <section class="card card--front" aria-label="Business card front">
    <div class="front__pattern" role="img" aria-label="Soft pink damask background pattern"></div>
    <div class="front__band"></div>
    <div class="front__label">
      <span class="brand-name">Sugar Loom</span>
    </div>
  </section>

  <section class="card card--back" aria-label="Business card back">
    <div class="back__swirl" role="img" aria-label="Faint blush floral swirl ornament"></div>
    <div class="back__brand">
      <span class="brand-name">Sugar Loom</span>
    </div>
    <div class="back__rule"></div>

    <div class="back__owner">
      <p class="owner__line">Sugar Loom by</p>
      <p class="owner__name">Dana Welch</p>
    </div>

    <ul class="social-list">
      <li><span class="social-mark"></span>sugarloomnyc</li>
      <li><span class="social-mark"></span>sugarloom_ny</li>
    </ul>

    <ul class="contact-list">
      <li>
        <svg viewBox="0 0 16 16" aria-hidden="true"><path d="M3 1h3l1 4-2 1c1 2 3 4 5 5l1-2 4 1v3c0 1-1 2-2 2C7 15 1 9 1 3c0-1 1-2 2-2z"/></svg>
        (516) 555-0147
      </li>
      <li>
        <svg viewBox="0 0 16 16" aria-hidden="true"><path d="M1 3h14v10H1z M2 4l6 5 6-5" fill="none" stroke="#2b2b2b" stroke-width="1.6"/></svg>
        hello@sugarloom.com
      </li>
      <li>
        <svg viewBox="0 0 16 16" aria-hidden="true"><circle cx="8" cy="8" r="6.5" fill="none" stroke="#2b2b2b" stroke-width="1.4"/><path d="M1.5 8h13M8 1.5c-3 3.5-3 9.5 0 13M8 1.5c3 3.5 3 9.5 0 13" fill="none" stroke="#2b2b2b" stroke-width="1.2"/></svg>
        www.sugarloomsweets.com
      </li>
    </ul>
  </section>
</body>
</html>
```